Heritage Hollow Business Cards

Require a business card design. <br/><br/>Needs to include logo (either round or long version) plus these details:<br/>Maya Torvell<br/>Heritage Hollow<br/>maya@kelvadtrading.com.au<br/>02 6481 7395<br/>PO Box Glenwarra NSW 2791<br/>www.heritagehollow.com.au<br/><br/>I need in an editable format so that I can create for multiple staff members. <br/><br/>

Target Market(s)

We are an online store selling renovation products to home owners are builders. Looking for a classic classy design.

Industry/Entity Type

Home And Garden

Contact Information for Business Card

Maya Torvell
Heritage Hollow
maya@kelvadtrading.com.au
02 6481 7395
PO Box Glenwarra NSW 2791
www.heritagehollow.com.au

Colors

Designer to choose colors to be used in the design.

Requirements
Must have
• Must include Logo.

```html
<!DOCTYPE html>
<html lang="en">
<head>
<meta charset="utf-8">
<title>Heritage Hollow Business Cards</title>
<link href="https://fonts.googleapis.com/css2?family=Work+Sans:wght@300;400;600;700&display=swap" rel="stylesheet">
<style>
  :root {
    --backdrop: #d9d9d9;
    --card-dark: #1a1a1a;
    --card-light: #ffffff;
    --ink: #111111;
    --ink-soft: #7a7a7a;
    --ink-reverse: #f2f2f2;
  }
  * { margin: 0; padding: 0; box-sizing: border-box; }
  html, body {
    width: 1200px; height: 930px; overflow: hidden;
    background: var(--backdrop);
    font-family: "Work Sans", Arial, sans-serif;
  }
  .stage { position: relative; width: 1200px; height: 930px; }
  .card {
    position: absolute;
    width: 560px; height: 320px;
    border-radius: 22px;
    box-shadow: 0 8px 22px rgba(0,0,0,0.18);
    overflow: hidden;
  }
  /* Back of card */
  .card--back { left: 90px; top: 90px; background: var(--card-dark); color: var(--ink-reverse); }
  .brand-seal {
    position: absolute; left: 185px; top: 40px;
    width: 190px; height: 190px;
    border: 1px solid rgba(255,255,255,0.75);
    border-radius: 50%;
    display: flex; align-items: center; justify-content: center;
    text-align: center;
  }
  .brand-seal__name {
    font-weight: 400; font-size: 30px; line-height: 1.05;
    color: var(--ink-reverse);
  }
  .web-line {
    position: absolute; left: 0; right: 0; top: 262px;
    text-align: center; font-size: 15px; letter-spacing: 3px;
    font-weight: 300; color: var(--ink-reverse);
  }
  .web-line strong { font-weight: 600; }

  /* Front of card */
  .card--front { left: 550px; top: 500px; background: var(--card-light); color: var(--ink); }
  .accent-tab {
    position: absolute; left: 0; top: 62px; width: 10px; height: 40px;
    background: var(--ink);
  }
  .person { position: absolute; left: 48px; top: 58px; }
  .person__name { font-weight: 700; font-size: 25px; letter-spacing: 0.5px; }
  .person__role { font-size: 13px; color: var(--ink-soft); margin-top: 2px; }
  .brand-mark {
    position: absolute; right: 48px; top: 70px;
    display: flex; align-items: center; gap: 12px;
  }
  .brand-mark__dot { width: 16px; height: 16px; border-radius: 50%; background: var(--ink); }
  .brand-mark__name { font-size: 28px; font-weight: 400; line-height: 1.05; color: var(--ink); }
  .contact { position: absolute; left: 48px; top: 178px; font-size: 14px; color: var(--ink-soft); }
  .contact__address { line-height: 1.35; margin-bottom: 8px; }
  .contact__row { display: flex; align-items: center; gap: 8px; height: 21px; }
  .contact__row strong { color: var(--ink); font-weight: 600; }
  .icon { width: 14px; height: 14px; flex: none; }
</style>
</head>
<body>
<div class="stage">
  <section class="card card--back">
    <div class="brand-seal">
      <span class="brand-seal__name">Heritage<br>Hollow</span>
    </div>
    <p class="web-line">www.<strong>heritagehollow</strong>.com.au</p>
  </section>

  <section class="card card--front">
    <div class="accent-tab"></div>
    <div class="person">
      <h1 class="person__name">Maya Torvell</h1>
      <p class="person__role">Director</p>
    </div>
    <div class="brand-mark">
      <span class="brand-mark__dot"></span>
      <span class="brand-mark__name">Heritage<br>Hollow</span>
    </div>
    <div class="contact">
      <p class="contact__address">PO Box Glenwarra<br>NSW 2791</p>
      <p class="contact__row">
        <svg class="icon" viewBox="0 0 14 14"><rect width="14" height="14" rx="3" fill="#111"/><path d="M4.2 3.2l1.6 1.6-.8 1.1c.6 1.2 1.6 2.2 2.8 2.8l1.1-.8 1.6 1.6-1 1.2C6.4 10.6 3.4 7.6 3 4.2z" fill="#fff"/></svg>
        02 6481 7395
      </p>
      <p class="contact__row">
        <svg class="icon" viewBox="0 0 14 14"><rect width="14" height="14" rx="3" fill="#111"/><rect x="3" y="4.2" width="8" height="5.6" fill="none" stroke="#fff" stroke-width="1"/><path d="M3 4.4l4 3 4-3" fill="none" stroke="#fff" stroke-width="1"/></svg>
        maya@kelvadtrading.com.au
      </p>
      <p class="contact__row">
        <svg class="icon" viewBox="0 0 14 14"><rect width="14" height="14" rx="3" fill="#111"/><circle cx="7" cy="7" r="3.8" fill="none" stroke="#fff" stroke-width="1"/><path d="M3.2 7h7.6M7 3.2c-2 2.3-2 5.3 0 7.6M7 3.2c2 2.3 2 5.3 0 7.6" fill="none" stroke="#fff" stroke-width="0.8"/></svg>
        www.<strong>heritagehollow</strong>.com.au
      </p>
    </div>
  </section>
</div>
</body>
</html>
```